SkyvornQ Business Cards and Stationary Design

Need a design for our business cards and stationary. I want to carry on the theme of the logo. I want the business cards to have a design on the back. I would like the business cards and the stationary to carry the same theme, design scheme, and branding

Target Market(s)

Airlines and Maintenance Facilities

Industry/Entity Type

Aviation

Contact Information for Business Card

Name
Position Title
Address: 4827 Trellis Hollow Road, Fort Pierce, Florida, 34951
Office Number
Mobile Number
Email
Website

Font styles to use
Serif
Sans Serif

Colors

Designer to choose colors to be used in the design.

```html
<!DOCTYPE html>
<html lang="en">
<head>
<meta charset="utf-8">
<title>SkyvornQ Business Card</title>
<link href="https://fonts.googleapis.com/css2?family=Roboto:wght@400;500;700&display=swap" rel="stylesheet">
<style>
  :root {
    --backdrop: #e9e7e3;
    --card: #ffffff;
    --navy: #1b3f7a;
    --sky: #1a9be0;
    --mid-blue: #2d6fb0;
    --ink: #3a3a3a;
    --grey: #555a60;
  }
  html, body {
    margin: 0;
    width: 1200px;
    height: 911px;
    overflow: hidden;
    background: var(--backdrop);
    font-family: "Roboto", Arial, sans-serif;
  }
  .canvas { position: relative; width: 1200px; height: 911px; }
  .card {
    position: absolute;
    width: 540px;
    height: 330px;
    background: var(--card);
    border-radius: 26px;
    box-shadow: 0 3px 0 #d6d6d6, 0 12px 30px rgba(0,0,0,0.18);
    overflow: hidden;
  }
  .card--front { left: 70px; top: 130px; }
  .card--back { left: 590px; top: 450px; }

  .brand-feature {
    position: absolute;
    right: 0;
    top: 0;
    width: 300px;
    height: 330px;
    background: linear-gradient(135deg, var(--sky) 0%, var(--mid-blue) 50%, var(--navy) 100%);
  }
  .contact { position: absolute; left: 34px; bottom: 34px; width: 200px; }
  .contact__name {
    margin: 0;
    font-size: 20px;
    font-weight: 700;
    color: var(--navy);
    letter-spacing: 0.5px;
    white-space: nowrap;
  }
  .contact__title {
    margin: 2px 0 14px;
    font-size: 12px;
    font-weight: 500;
    color: var(--sky);
    letter-spacing: 0.5px;
  }
  .contact__address {
    margin: 0 0 10px;
    font-size: 11px;
    line-height: 1.45;
    color: var(--ink);
  }
  .contact__list { list-style: none; margin: 0; padding: 0; }
  .contact__item {
    display: flex;
    align-items: center;
    gap: 8px;
    font-size: 11px;
    line-height: 1.6;
    color: var(--ink);
  }
  .contact__icon { width: 10px; height: 10px; fill: var(--grey); flex: none; }

  .back__layout {
    position: absolute;
    inset: 0;
    display: flex;
    flex-direction: column;
    align-items: center;
    justify-content: center;
    gap: 22px;
  }
  .back__web {
    font-size: 12px;
    letter-spacing: 6px;
    color: var(--grey);
  }
  .back__name {
    font-size: 38px;
    font-weight: 700;
    color: var(--navy);
    letter-spacing: 4px;
    line-height: 1;
  }
  .back__mark {
    width: 44px;
    height: 44px;
    border-radius: 50%;
    background: var(--navy);
  }
</style>
</head>
<body>
<main class="canvas">
  <section class="card card--front">
    <div class="brand-feature" role="img" aria-label="Large brand decoration in blue gradient"></div>
    <div class="contact">
      <h1 class="contact__name">MAREK DELBROOK</h1>
      <p class="contact__title">CEO/FOUNDER</p>
      <p class="contact__address">4827 Trellis Hollow Road<br>Fort Pierce, Florida, 34951</p>
      <ul class="contact__list">
        <li class="contact__item">
          <svg class="contact__icon" viewBox="0 0 10 10"><path d="M2 0.5 L3.8 2.6 L2.9 3.7 Q4 6 6.3 7.1 L7.4 6.2 L9.5 8 L8.2 9.5 Q1.5 8.5 0.5 1.8 Z"/></svg>
          555 014 2738
        </li>
        <li class="contact__item">
          <svg class="contact__icon" viewBox="0 0 10 10"><path d="M2.5 0 H7.5 V10 H2.5 Z M3.3 1 V8 H6.7 V1 Z" fill-rule="evenodd"/></svg>
          555 018 9364
        </li>
        <li class="contact__item">
          <svg class="contact__icon" viewBox="0 0 10 10"><path d="M0 2 H10 V8 H0 Z M0.8 2.6 L5 5.5 L9.2 2.6 Z" fill-rule="evenodd"/></svg>
          info@skyvornq.com
        </li>
        <li class="contact__item">
          <svg class="contact__icon" viewBox="0 0 10 10"><circle cx="5" cy="5" r="5"/></svg>
          www.skyvornq.com
        </li>
      </ul>
    </div>
  </section>

  <section class="card card--back">
    <div class="back__layout">
      <span class="back__web">www.skyvornq.com</span>
      <span class="back__name">SKYVORNQ</span>
      <span class="back__mark"></span>
    </div>
  </section>
</main>
</body>
</html>
```